regPersonal Trainer Flyer Design

Project Deadline Extended
Reason: I have been very busy with other work and would like to extend the deadline to offer designers the chance to edit and improve designs with my help. Thank you for all the designs that have been sent so far.

```html
<!DOCTYPE html>
<html lang="en">
<head>
<meta charset="utf-8">
<title>Personal Trainer Flyer</title>
<link href="https://fonts.googleapis.com/css2?family=Open+Sans:ital,wght@0,400;0,600;0,700;1,400&family=Arimo:wght@700&display=swap" rel="stylesheet">
<style>
  :root {
    --blue: #0f9ad8;
    --blue-deep: #0a5fa8;
    --charcoal: #3a3a3c;
    --slate: #4a4a4d;
    --grey-light: #d9d9d9;
    --grey-mid: #bfbfbf;
    --white: #ffffff;
    --text-dark: #333333;
  }
  * { margin: 0; padding: 0; box-sizing: border-box; }
  html, body { width: 1200px; height: 1000px; overflow: hidden; background: var(--white); }
  body { font-family: "Open Sans", Arial, sans-serif; }
  .canvas { position: relative; width: 1200px; height: 1000px; }
  .artwork { position: absolute; left: 0; top: 0; }

  .offer-banner {
    position: absolute; left: 600px; top: 252px; width: 340px;
    text-align: right; color: var(--white);
    font-weight: 700; font-size: 25px; line-height: 28px; letter-spacing: 0.2px;
  }
  .offer-lead {
    position: absolute; left: 600px; top: 284px; width: 340px;
    text-align: right; color: var(--text-dark);
    font-size: 21px; line-height: 26px;
  }
  .offer-highlight {
    position: absolute; left: 580px; top: 302px; width: 362px;
    text-align: right; color: var(--blue);
    font-family: "Arimo", Arial, sans-serif; font-weight: 700;
    font-size: 36px; line-height: 42px;
  }

  .pain-points {
    position: absolute; left: 675px; top: 362px; list-style: none;
    font-style: italic; font-size: 21px; line-height: 25.5px; color: var(--text-dark);
  }
  .pain-points li { position: relative; padding-left: 18px; }
  .pain-points li::before {
    content: ""; position: absolute; left: 0; top: 10px;
    width: 7px; height: 7px; border-radius: 50%; background: var(--blue);
  }

  .benefits {
    position: absolute; left: 640px; top: 474px; width: 300px;
    text-align: right; color: var(--blue); font-size: 16.5px; line-height: 22px;
  }

  .trainer-contact {
    position: absolute; left: 700px; top: 579px; width: 234px;
    text-align: right; color: var(--text-dark);
  }
  .trainer-name { font-size: 18px; line-height: 24px; }
  .trainer-role { font-size: 12.5px; line-height: 14px; color: var(--blue); }
  .trainer-phone { font-size: 19px; font-weight: 700; line-height: 24px; letter-spacing: 0.5px; }
  .trainer-email { font-size: 12px; line-height: 16px; color: var(--blue); }

  .brand-main {
    position: absolute; left: 706px; top: 688px; display: flex; align-items: center;
  }
  .brand-mark { width: 46px; height: 46px; background: var(--slate); }
  .brand-divider { width: 1px; height: 70px; background: var(--grey-mid); margin: 0 6px 0 28px; }
  .brand-name { font-size: 25px; font-weight: 400; color: var(--blue); line-height: 30px; }

  .brand-faint {
    position: absolute; left: 256px; top: 700px; width: 84px; text-align: center;
  }
  .brand-faint-mark { width: 30px; height: 22px; margin: 0 auto 4px; background: #6a6a6d; }
  .brand-faint-name { font-size: 13px; color: #8a8a8d; line-height: 16px; }
</style>
</head>
<body>
<div class="canvas">
  <svg class="artwork" width="1200" height="1000" viewBox="0 0 1200 1000">
    <defs>
      <linearGradient id="photoTone" x1="0" y1="0" x2="1" y2="1">
        <stop offset="0" stop-color="#6d9fc4"/>
        <stop offset="0.5" stop-color="#2f86c9"/>
        <stop offset="1" stop-color="#1c4f8a"/>
      </linearGradient>
      <linearGradient id="greyBand" x1="0" y1="0" x2="1" y2="0">
        <stop offset="0" stop-color="#e8e8e8"/>
        <stop offset="1" stop-color="#cfcfcf"/>
      </linearGradient>
      <linearGradient id="blueWedge" x1="0" y1="0" x2="1" y2="1">
        <stop offset="0" stop-color="#1aa3e0"/>
        <stop offset="1" stop-color="#0a5fa8"/>
      </linearGradient>
    </defs>

    <!-- photo panel -->
    <polygon class="photo-area" role="img"
      aria-label="Photo: personal trainer coaching a woman doing a barbell squat in front of a blue-tinted brick wall"
      points="243,232 478,232 530,386 498,462 612,768 376,768 243,452"
      fill="url(#photoTone)"/>

    <!-- dark chevron band -->
    <polygon class="chevron-band" points="480,232 515,232 573,390 536,462 652,768 618,768 504,462 536,388" fill="var(--charcoal)"/>

    <!-- lower left corner -->
    <polygon class="corner-dark" points="243,460 370,768 243,768" fill="var(--slate)"/>
    <polygon class="corner-blue" points="243,478 305,632 243,600" fill="url(#blueWedge)"/>

    <!-- headline bands -->
    <polygon class="offer-band" points="582,250 957,250 957,280 600,280" fill="var(--blue)"/>
    <polygon class="lead-band" points="596,281 957,281 957,346 624,346" fill="url(#greyBand)"/>
  </svg>

  <div class="brand-faint">
    <div class="brand-faint-mark"></div>
    <div class="brand-faint-name">SamHollins</div>
  </div>

  <div class="offer-banner">INTRODUCTORY OFFER</div>
  <div class="offer-lead">contact me now for</div>
  <div class="offer-highlight">one free session</div>

  <ul class="pain-points">
    <li>Lacking motivation?</li>
    <li>Not achieving your goals?</li>
    <li>Need help?</li>
    <li>Bored of the gym?</li>
  </ul>

  <div class="benefits">
    You're never too old<br>
    I can help improve your health<br>
    and well-being<br>
    Training can be at your home
  </div>

  <div class="trainer-contact">
    <div class="trainer-name">Sam Hollins</div>
    <div class="trainer-role">Personal Trainer</div>
    <div class="trainer-phone">07700900481</div>
    <div class="trainer-email">samhollins@postbox.co.uk</div>
  </div>

  <div class="brand-main">
    <div class="brand-mark"></div>
    <div class="brand-divider"></div>
    <div class="brand-name">SamHollins</div>
  </div>
</div>
</body>
</html>
```